Dog grooming business card
This is a business card for m dog grooming business like it say above.
In the priorities box below I will have the text that I want on the card.

Industry/Entity Type

Business

Colors

Designer to choose colors to be used in the design.

Requirements
Must have
• My logo and the insurance stamp must be on the card.

Text it must have :

Professional grooming services
Email: lunabrisk@mailvale.net
Text or call 1 705 318 6052
TWF certified/member
Pet first aid certified
Next appointment ___________________________________
Nice to have
• Greens to match my logo

```html
<!DOCTYPE html>
<html lang="en">
<head>
<meta charset="utf-8">
<title>Luna Brisk – Business Card</title>
<link href="https://fonts.googleapis.com/css2?family=Alike&display=swap" rel="stylesheet">
<style>
  :root {
    --page-bg: #e9e5df;
    --card-bg: #ffffff;
    --ink: #1c1c1a;
    --brand-green: #7fb437;
    --badge-blue: #2a6bc0;
    --rule: #3a3a36;
    --watermark-grey: #e4e4e4;
  }
  * { box-sizing: border-box; margin: 0; padding: 0; }
  html, body {
    width: 1200px;
    height: 870px;
    overflow: hidden;
    background: var(--page-bg);
  }
  .canvas {
    width: 1200px;
    height: 870px;
    display: flex;
    justify-content: center;
    align-items: center;
    gap: 60px;
    font-family: "Alike", Georgia, serif;
    color: var(--ink);
  }
  .card {
    position: relative;
    width: 400px;
    height: 680px;
    background: var(--card-bg);
    box-shadow: 0 10px 28px rgba(0, 0, 0, 0.18);
    overflow: hidden;
  }
  .brand {
    display: flex;
    align-items: center;
    justify-content: center;
    gap: 14px;
    font-size: 44px;
    color: var(--brand-green);
    line-height: 1;
  }
  .brand-dot {
    width: 30px;
    height: 30px;
    border-radius: 50%;
    background: var(--brand-green);
    flex: none;
  }
  .card-front .brand { position: absolute; top: 96px; left: 0; right: 0; }
  .details {
    position: absolute;
    top: 268px;
    left: 0;
    right: 0;
    text-align: center;
    font-size: 24px;
    line-height: 1.58;
    letter-spacing: 0.3px;
  }
  .appointment {
    position: absolute;
    top: 508px;
    left: 30px;
    right: 30px;
    display: flex;
    align-items: flex-end;
    gap: 14px;
    font-size: 24px;
  }
  .appointment-line {
    flex: 1;
    border-bottom: 1.5px solid var(--rule);
    margin-bottom: 8px;
  }
  .insurance-badge {
    position: absolute;
    right: 24px;
    bottom: 28px;
    width: 150px;
    height: 74px;
    border: 2.5px solid var(--badge-blue);
    border-radius: 12px;
    background: #f4f8fd;
  }
  .card-back .brand { position: absolute; top: 150px; left: 0; right: 0; font-size: 48px; }
  .back-watermark {
    position: absolute;
    top: 320px;
    left: 0;
    width: 300px;
    height: 310px;
    border-radius: 0 140px 140px 0;
    background: linear-gradient(160deg, var(--watermark-grey), #f2f2f2);
  }
</style>
</head>
<body>
  <main class="canvas">
    <section class="card card-front">
      <div class="brand"><span class="brand-dot"></span><span class="brand-name">Luna Brisk</span></div>
      <div class="details">
        <p>Professional grooming services</p>
        <p>1 705 318 6052</p>
        <p>lunabrisk@mailvale.net</p>
        <p>TWF certified/member</p>
        <p>Pet first aid certified</p>
      </div>
      <div class="appointment">
        <span class="appointment-label">Next appointment</span>
        <span class="appointment-line"></span>
      </div>
      <div class="insurance-badge" role="img" aria-label="Pet care insurance stamp"></div>
    </section>

    <section class="card card-back">
      <div class="brand"><span class="brand-dot"></span><span class="brand-name">Luna Brisk</span></div>
      <div class="back-watermark" role="img" aria-label="Large faint grey dog silhouette decoration"></div>
    </section>
  </main>
</body>
</html>
```